Church Website with Home Page and Member Sermon Library

I am in need of an updated design for our church website. This will include 4 pages (outlined below). We are a conservative, evangelical, Christian church. The site should be modern and clean, while still reflecting our conservative values. I already have a logo for our church, and I want the site to incorporate the logo, and match the logo/branding. Stock photos are allowed if needed, but I have uploaded some images of our church and would prefer those images to be used if possible. Any stock photos used should not include any people in the photos (scenery, nature, buildings, animals, etc. are fine).

The site will need 4 pages: Home, Support Us (Donate), Login, and Recording Library.

Page 1: Home
The home page should include the following sections:

- Navigation: Should include links to each section of the home page plus a "listen live" link which will take the user to a live-streaming site and a "support us" link which will take the user to a support/donate page.

- Announcements: Can be either a banner or some other design, but there needs to be some way for us to post announcements for visitors to see. I'm open for creative ideas in this section, but would like it not to take up a lot of room on the page.

- About Us: Should include address, service times (see attached document), and information about the church.

- Pastor Bio: A section that introduces our pastor and gives a short bio about our pastor. Would like this section to include a picture of our pastor. Somewhere in this section I would like to include this Bible reference: "And I will give you pastors according to mine heart, which shall feed you with knowledge and understanding. Jer 3:15 LPW"

- Articles of Faith (What We Believe): This should include several sub-sections each with a heading, body, and possibly 1 or more scripture references. I have attached a document to the brief that includes our articles of faith. Feel free to be creative with this section in how you lay these out and format them.

- Support Us: A small section that explains what kind of support someone can give and a link to a donation page. The link can say something like "Support Us" or "Donate Now".

- Contact form: A contact form that allows the visitor to send us a message. The contact form should ask for name, email, phone, and message.

- Footer: A footer that will be displayed on all pages of the site. This should include at a minimum a link to the home page (or a link to each individual section in the home page if you prefer), a link to "listen live", a link to "support us", a link to "contact us" (or you can put the contact form directly in the footer if you prefer), the address, and a "member login" link.

Page 2: Support Us
The donation page should include a form the visitor can fill out to make a donation. We will embed a third party form later. For this design, please just mock out the design with a basic form asking for name, phone, and email.

Page 3: Login
The recording library (detailed below) will require members to login with a shared numeric code before accessing the page. We need a design for a login screen. The screen should include navigation/footer just like all other pages, but the body of the login page will consist only of a form that asks the user to enter the access code and then a "login" button.

Page 4: Recording Library

The library page is a member-only page that will require a shared, numeric pass code to access. On this page, members will be able to access a filterable list of past sermons. The page by default should display most recent sermons, but should also include a search form that allows the member to filter the sermon list to find a particular sermon. The search form should allow the user to select a filter type (e.g. Speaker name, date, event, etc.) and type in a value to search. They should be able to add multiple filters and remove filters that have been added. Each sermon that is displayed in the result list should include basic information such as title, date, speaker, tags, etc. along with a download icon, and an embedded audio player where they can click a play button to stream it on-demand. Each sermon should also have clickable tags associated with it that can be used to find related sermons.
Updates

I have uploaded several images of our church. Feel free to incorporate these into your design if possible.

Target Market(s)

Church Members

Industry/Entity Type

Religion

Number of Pages Required

4 page

Font styles to use
Sans Serif

Colors

Designer to choose colors to be used in the design.

Requirements
Must have
• Must incorporate the logo (attached)
Nice to have
• Would like the design to incorporate pictures of our church (attached) instead of stock photos if possible.
Should not have
• Please avoid an overly cluttered design. Stock photos used should not include any people in the photos.

```html
<!DOCTYPE html>
<html lang="en">
<head>
<meta charset="utf-8">
<title>Grace Hollow Church</title>
<link href="https://fonts.googleapis.com/css2?family=Playfair+Display:wght@400;700&family=Libre+Caslon+Display&family=Great+Vibes&family=Roboto:wght@400;500;700&display=swap" rel="stylesheet">
<style>
:root{
  --teal:#05b6d4;
  --teal-bright:#1cc7de;
  --green:#7ab55c;
  --green-dark:#6aa64f;
  --ink:#2f2f2f;
  --body:#5f5f5f;
  --page:#f4faf9;
  --white:#ffffff;
  --footer:#2d2d2d;
  --field:#ececec;
}
*{margin:0;padding:0;box-sizing:border-box}
html,body{width:1200px;height:3583px;overflow:hidden}
body{position:relative;background:var(--page);font-family:'Roboto',sans-serif;color:var(--body)}
.abs{position:absolute}
.serif{font-family:'Libre Caslon Display',serif;font-weight:400}
.center{text-align:center}
p.copy{font-size:11.5px;line-height:17px;color:var(--body)}

/* hero */
.hero{position:absolute;left:0;top:0;width:1200px;height:716px;overflow:hidden;background:var(--white)}
.hero-photo{position:absolute;left:0;top:0;width:1200px;height:716px}
.brand{position:absolute;left:0;width:1200px;text-align:center;font-family:'Playfair Display',serif;font-weight:400;color:var(--green);letter-spacing:3px}
.nav{position:absolute;top:125px;left:0;width:1200px;display:flex;justify-content:center;gap:42px;font-family:'Playfair Display',serif;font-size:13px;letter-spacing:1px;color:#444}
.nav a{color:inherit;text-decoration:none}
.nav a.active{font-weight:700;color:#222}
.donate-ribbon{position:absolute;left:958px;top:0;width:79px;height:97px}
.hero-script{position:absolute;top:288px;width:1200px;text-align:center;font-family:'Great Vibes',cursive;font-size:38px;color:var(--white)}
.hero-title{position:absolute;top:326px;width:1200px;text-align:center;font-family:'Playfair Display',serif;font-weight:700;font-size:48px;color:var(--white);letter-spacing:1px}
.pill{position:absolute;display:flex;align-items:center;justify-content:center;border-radius:30px;text-decoration:none}
.btn-live{left:503px;top:398px;width:194px;height:42px;background:var(--green);color:var(--white);font-family:'Playfair Display',serif;font-weight:700;font-size:11.5px}

/* about */
.about-eyebrow{left:640px;top:770px;font-family:'Playfair Display',serif;font-size:21px;color:var(--teal)}
.about-heading{left:638px;top:805px;width:390px;font-size:32px;line-height:38px;color:#3a3a3a}
.btn-solid{background:var(--teal);color:var(--white);font-size:11.5px;font-weight:700}

/* announcement */
.ann-title{left:0;top:1218px;width:1200px;font-size:38px;color:#3a3a3a}
.ann-box{left:161px;top:1290px;width:877px;height:215px;background:var(--teal-bright)}
.ann-head{left:161px;width:877px;top:1326px;font-size:30px;color:var(--white)}
.ann-sub{left:161px;width:877px;top:1362px;font-family:'Playfair Display',serif;font-size:14px;color:var(--white)}
.ann-date{left:490px;top:1391px;width:180px;height:29px;background:var(--green);color:var(--white);font-size:11.5px}
.ann-copy{left:260px;width:680px;top:1436px;font-size:11.5px;line-height:17px;color:var(--white);text-align:center}

/* services */
.service{position:absolute;top:1690px;width:220px;text-align:center;transform:translateX(-50%)}
.service h3{font-family:'Playfair Display',serif;font-weight:700;font-size:19px;line-height:20px;color:var(--white)}
.service .time{margin:22px auto 0;width:66px;height:66px;border-radius:50%;background:var(--white);display:flex;align-items:center;justify-content:center;font-weight:700;font-size:12px;color:#222}

/* pastor */
.pastor-title{left:158px;top:1945px;font-size:53px;color:#333}

/* support */
.support-eyebrow{top:2410px;left:0;width:1200px;font-family:'Playfair Display',serif;font-size:13px;letter-spacing:3px;color:var(--teal)}
.support-sub{top:2429px;left:0;width:1200px;font-size:23px;color:#333}
.support-title{top:2458px;left:0;width:1200px;font-size:35px;color:#222}
.btn-outline{left:505px;top:2595px;width:189px;height:53px;border:1.5px solid var(--teal);color:var(--teal);font-size:11.5px;font-weight:500}

/* articles */
.faith-title{top:2705px;left:0;width:1200px;font-size:58px;color:#2c2c2c}
.article{position:absolute;width:310px}
.article .badge{position:absolute;left:-36px;top:2px;width:24px;height:32px}
.article h4{font-family:'Libre Caslon Display',serif;font-weight:400;font-size:20px;color:#333;margin-bottom:6px}
.article p{font-size:10.5px;line-height:15.5px;color:var(--body);margin-bottom:6px}

/* footer */
.footer-nav{position:absolute;left:161px;top:3405px;display:flex;gap:34px;font-family:'Playfair Display',serif;font-size:13px;color:var(--white);letter-spacing:1px}
.footer-nav a{color:inherit;text-decoration:none}
.footer-nav a.active{font-weight:700}
.field{position:absolute;background:var(--field);font-size:9px;letter-spacing:1px;color:#777;padding:0 14px;display:flex;align-items:center}
.field.msg{align-items:flex-start;padding-top:10px}
.submit{position:absolute;left:734px;top:3454px;width:304px;height:31px;background:var(--green);color:var(--white);font-weight:700;font-size:13px;display:flex;align-items:center;justify-content:center}
.social{position:absolute;top:3448px;width:10px;height:10px;border-radius:50%;background:var(--white)}
.rule{position:absolute;left:161px;top:3520px;width:877px;height:1px;background:#4a4a4a}
.legal{position:absolute;top:3543px;left:0;width:1200px;text-align:center;font-size:9px;letter-spacing:.5px;color:#bdbdbd}
</style>
</head>
<body>

<header class="hero">
  <svg class="hero-photo" viewBox="0 0 1200 716" role="img" aria-label="Photograph of the brick church building and its parking lot under an overcast sky">
    <defs>
      <linearGradient id="heroTone" x1="0" y1="0" x2="0" y2="1">
        <stop offset="0" stop-color="#e2e2e1"/>
        <stop offset=".35" stop-color="#c9bdb4"/>
        <stop offset=".6" stop-color="#a8968a"/>
        <stop offset="1" stop-color="#b4b1ae"/>
      </linearGradient>
    </defs>
    <rect width="1200" height="716" fill="url(#heroTone)"/>
    <path d="M0 630 C200 600 380 640 560 610 C760 578 960 630 1200 595 L1200 716 L0 716 Z" fill="#ffffff"/>
  </svg>

  <div class="brand" style="top:56px;font-size:22px;line-height:26px">GRACE HOLLOW</div>
  <nav class="nav">
    <a class="active" href="#">HOME</a>
    <a href="#">SUPPORT US</a>
    <a href="#">LOGIN</a>
  </nav>

  <svg class="donate-ribbon" viewBox="0 0 79 97">
    <path d="M0 0 H79 V97 L39.5 80 L0 97 Z" fill="var(--teal)"/>
    <path d="M39.5 40 C30 33 24 27 24 21 C24 15 29 12 33 12 C36 12 38 14 39.5 16 C41 14 43 12 46 12 C50 12 55 15 55 21 C55 27 49 33 39.5 40 Z" fill="none" stroke="#fff" stroke-width="2"/>
    <text x="39.5" y="60" text-anchor="middle" font-family="Playfair Display, serif" font-weight="700" font-size="11" fill="#fff" letter-spacing="1">DONATE</text>
  </svg>

  <div class="hero-script">Grace Hollow Church</div>
  <h1 class="hero-title">LIFE. PLACE. MEANING.</h1>
  <a class="pill btn-live" href="#">LISTEN LIVE ON STREAMHALL</a>
</header>

<section class="about">
  <svg class="abs" style="left:163px;top:746px" width="426" height="422" viewBox="0 0 426 422" role="img" aria-label="Photograph of the church entrance and sign">
    <defs>
      <linearGradient id="aboutPhoto" x1="0" y1="0" x2="0" y2="1">
        <stop offset="0" stop-color="#d8d8d7"/>
        <stop offset=".45" stop-color="#ad9283"/>
        <stop offset="1" stop-color="#c4c1be"/>
      </linearGradient>
    </defs>
    <rect x="0" y="0" width="426" height="422" rx="24" fill="url(#aboutPhoto)"/>
  </svg>
  <div class="abs about-eyebrow">About Grace Hollow Church</div>
  <h2 class="abs about-heading serif">The church will help you find your way to God and love</h2>
  <div class="abs" style="left:640px;top:892px;width:56px;height:3px;border-radius:2px;background:var(--green)"></div>
  <p class="abs copy" style="left:636px;top:917px;width:400px">Lorem ipsum dolor sit amet, consectetur adipiscing elit. Nullam eu blandit leo. Mauris et nibh nibh. Pellentesque iaculis odio varius, rutrum dui sed, consectetur eros. Suspendisse potenti.</p>
  <p class="abs copy" style="left:636px;top:993px;width:400px">Nam varius porta tortor eu consequat. Curabitur at mattis eros, quis lacinia arcu. Lorem ipsum dolor sit amet, consectetur adipiscing elit. Nullam eu blandit leo. Mauris et nibh nibh. Pellentesque iaculis odio varius, rutrum dui sed, consectetur eros. Suspendisse potenti. Nam varius porta tortor eu consequat. Curabitur at mattis eros</p>
  <a class="pill btn-solid" style="left:635px;top:1098px;width:145px;height:43px" href="#">DONATE NOW</a>
</section>

<section class="announcement">
  <h2 class="abs ann-title serif center">Announcement</h2>
  <div class="abs ann-box"></div>
  <svg class="abs" style="left:161px;top:1290px" width="877" height="215" viewBox="0 0 877 215">
    <path d="M45 111 H10 M10 111 l7 -6 M10 111 l7 6" stroke="#fff" stroke-width="1.6" fill="none" stroke-linecap="round"/>
    <path d="M827 111 H862 M862 111 l-7 -6 M862 111 l-7 6" stroke="#fff" stroke-width="1.6" fill="none" stroke-linecap="round"/>
  </svg>
  <div class="abs ann-head serif center">Interested in membership?</div>
  <div class="abs ann-sub center">Join us for on April 30th!</div>
  <div class="pill ann-date">April 30, 2023</div>
  <p class="abs ann-copy">Lorem ipsum dolor sit amet, consectetur adipiscing elit. Nullam eu blandit leo. Mauris et nibh nibh. Pellentesque iaculis odio varius, rutrum dui sed, consectetur eros. Suspendisse potenti.</p>
</section>

<section class="services">
  <svg class="abs" style="left:0;top:1570px" width="1200" height="256" viewBox="0 0 1200 256" role="img" aria-label="Green-tinted photograph of the town skyline behind the service times">
    <path d="M0 60 C150 30 300 30 420 70 C520 105 620 105 760 50 C880 10 1020 30 1200 40 L1200 256 L0 256 Z" fill="var(--green-dark)"/>
  </svg>
  <div class="service" style="left:259px"><h3>Wednesday<br>Evening Service:</h3><div class="time">7:30 PM</div></div>
  <div class="service" style="left:484px"><h3>Sunday<br>School:</h3><div class="time">10:00 AM</div></div>
  <div class="service" style="left:703px"><h3>Sunday<br>Morning Service:</h3><div class="time">11:00 AM</div></div>
  <div class="service" style="left:934px"><h3>Sunday<br>Evening Service:</h3><div class="time">05:30 PM</div></div>
</section>

<section class="pastor">
  <h2 class="abs pastor-title serif">Pastor Bio</h2>
  <p class="abs copy" style="left:160px;top:2013px;width:425px">Lorem ipsum dolor sit amet, consectetur adipiscing elit. Nullam eu blandit leo. Mauris et nibh nibh. Pellentesque iaculis odio varius, rutrum dui sed, consectetur eros. Suspendisse potenti. Nam varius porta tortor eu consequat. Curabitur at mattis eros, quis lacinia arcu. Lorem ipsum dolor sit amet, consectetur adipiscing elit. Nullam eu blandit leo. Mauris et nibh nibh. Pellentesque iaculis odio varius, rutrum dui sed, consectetur eros. Suspendisse potenti. Nam varius porta tortor eu consequat. Curabitur at mattis eros</p>
  <p class="abs copy" style="left:160px;top:2157px;width:425px">Pellentesque iaculis odio varius, rutrum dui sed, consectetur eros. Suspendisse potenti. Nam varius porta tortor eu consequat. Curabitur at mattis Lorem ipsum dolor sit amet, consectetur adipiscing elit. Nullam eu blandit leo. Mauris et nibh nibh. Pellentesque iaculis odio varius, rutrum dui sed, consectetur eros. Suspendisse potenti. Nam varius porta tortor eu consequat.</p>
  <svg class="abs" style="left:640px;top:1880px" width="350" height="440" viewBox="0 0 350 440" role="img" aria-label="Portrait of the pastor">
    <rect x="0" y="0" width="350" height="440" rx="24" fill="#e4e4e4"/>
    <text x="175" y="232" text-anchor="middle" font-family="Roboto, sans-serif" font-weight="700" font-size="34" fill="#b5b5b5">150x150</text>
  </svg>
</section>

<section class="support">
  <div class="abs support-eyebrow center">Grace Hollow Church</div>
  <div class="abs support-sub serif center">Become a part of our community.</div>
  <h2 class="abs support-title serif center">We really appreciate all your donations.</h2>
  <p class="abs copy center" style="left:230px;top:2519px;width:740px">Lorem ipsum dolor sit amet, consectetur adipiscing elit. Nullam eu blandit leo. Mauris et nibh nibh. Pellentesque iaculis odio varius, rutrum dui sed, consectetur eros. Suspendisse potenti. Nam varius porta tortor eu consequat. Curabitur at mattis eros, quis lacinia arcu. Lorem ipsum dolor sit amet, consectetur</p>
  <a class="pill btn-outline" href="#">MAKE DONATION</a>
</section>

<section class="articles">
  <h2 class="abs faith-title serif center">Articles of Faith</h2>

  <svg width="0" height="0" style="position:absolute">
    <defs><symbol id="badge" viewBox="0 0 24 32"><path d="M0 0 H24 V32 L12 25 L0 32 Z" fill="var(--green)"/></symbol></defs>
  </svg>

  <div class="article" style="left:89px;top:2810px;width:305px">
    <svg class="badge"><use href="#badge"/><text x="12" y="17" text-anchor="middle" font-size="9" font-weight="700" fill="#fff" font-family="Roboto, sans-serif">01</text></svg>
    <h4>The God Head.</h4>
    <p>We believe in the God head bodily, known as the Divine Trinity. This body consist of God the father, Jesus Christ, his only begotten son and the redeemer of the world, and of the Holy Ghost, The third person of the Divine Trinity.</p>
  </div>
  <div class="article" style="left:89px;top:2935px;width:305px">
    <svg class="badge"><use href="#badge"/><text x="12" y="17" text-anchor="middle" font-size="9" font-weight="700" fill="#fff" font-family="Roboto, sans-serif">02</text></svg>
    <h4>Full Salvation.</h4>
    <p>We believe that Salvation is received only when a person comes to the realization that he or she is lost and separated from God and becomes full of godly sorrow, confessing their sins and true repentance, believing in the shed blood of the Lord Jesus Christ as the only sacrifice for sins. Through the blood of Christ we have:</p>
    <p>(1) remission of sins, Matthew 26:28 Heb 9:22<br>(2) Sanctification. Hebrews 13:12<br>(3) redemption. Revelations 5:9<br>(4) cleansing. 1 John 1:7 Rev. 1:5<br>(5). Justification. Romans 5:9</p>
  </div>

  <div class="article" style="left:452px;top:2810px;width:305px">
    <svg class="badge"><use href="#badge"/><text x="12" y="17" text-anchor="middle" font-size="9" font-weight="700" fill="#fff" font-family="Roboto, sans-serif">03</text></svg>
    <h4>Sanctification.</h4>
    <p>"Sanctify them through thy truth thy word is truth St John 17:17. For this is the will of God even your sanctification"</p>
    <p>We believe in a set apart life, separate from the world to Christ 2 Cor 6:17-18</p>
  </div>
  <div class="article" style="left:452px;top:2938px;width:305px">
    <svg class="badge"><use href="#badge"/><text x="12" y="17" text-anchor="middle" font-size="9" font-weight="700" fill="#fff" font-family="Roboto, sans-serif">04</text></svg>
    <h4>Baptism of the Holy Ghost.</h4>
    <p>We believe in the baptism of the Holy Ghost as it is taught in the Bible and promised by our Lord Jesus Christ, with speaking in tongues as the Spirit gives utterance as the initial evidence. Acts 2:4 we believe</p>
  </div>
  <div class="article" style="left:452px;top:3060px;width:305px">
    <svg class="badge"><use href="#badge"/><text x="12" y="17" text-anchor="middle" font-size="9" font-weight="700" fill="#fff" font-family="Roboto, sans-serif">05</text></svg>
    <h4>Divine Healing.</h4>
    <p>We believe Divine Healing to be included in the atonement of Jesus Christ our Lord, And believe that it is still for us today. 1 Peter 2:24 Luke 9:1-2 Mark 16-18 James 5:15</p>
  </div>

  <div class="article" style="left:813px;top:2810px;width:310px">
    <svg class="badge"><use href="#badge"/><text x="12" y="17" text-anchor="middle" font-size="9" font-weight="700" fill="#fff" font-family="Roboto, sans-serif">06</text></svg>
    <h4>Second coming of Christ.</h4>
    <p>We believe in the second coming of Jesus Christ. Matthew 24:44 Luke 12:40</p>
  </div>
  <div class="article" style="left:813px;top:2902px;width:310px">
    <svg class="badge"><use href="#badge"/><text x="12" y="17" text-anchor="middle" font-size="9" font-weight="700" fill="#fff" font-family="Roboto, sans-serif">07</text></svg>
    <h4>Eternity</h4>
    <p>We believe in Literal Eternity. Eternal Life for the believer and eternal death for those without Christ. Revelations 21:1-27</p>
  </div>
</section>

<footer class="site-footer">
  <svg class="abs" style="left:0;top:3200px" width="1200" height="383" viewBox="0 0 1200 383">
    <path d="M0 90 C180 40 380 40 600 70 C820 100 1020 60 1200 40 L1200 383 L0 383 Z" fill="var(--footer)"/>
  </svg>

  <nav class="footer-nav">
    <a class="active" href="#">HOME</a>
    <a href="#">SUPPORT US</a>
    <a href="#">LOGIN</a>
  </nav>

  <div class="brand" style="top:3398px;font-size:20px;line-height:24px;color:#e6e6e6">GRACE HOLLOW</div>
  <span class="social" style="left:563px"></span>
  <span class="social" style="left:595px"></span>
  <span class="social" style="left:627px"></span>

  <div class="field" style="left:734px;top:3340px;width:150px;height:28px">NAME</div>
  <div class="field" style="left:889px;top:3340px;width:149px;height:28px">EMAIL</div>
  <div class="field" style="left:734px;top:3374px;width:304px;height:29px">PHONE NO</div>
  <div class="field msg" style="left:734px;top:3408px;width:304px;height:40px">MESSAGE</div>
  <div class="submit">SUBMIT</div>

  <div class="rule"></div>
  <div class="legal">© GRACE HOLLOW CHURCH. ALL RIGHTS RESERVED - 2023</div>
</footer>

</body>
</html>
```